Powerpoint, Graphics for Sermon Series

I am starting a sermon series on the short letters if Scripture that are between Hebrews and Revelation. The sermon series will be called "Walking Unmarked Trails: Lasting Lessons from Quiet Hills."

Think about finding a packet of letters in an Attic. There is only the dialogue of the writer. We don't know exactly what the receivers were going through or even what their response to the letters were/are!

Target Market(s)

Local Church

Industry/Entity Type

Christian

Font styles to use
Serif
Sans Serif

Colors

Designer to choose colors to be used in the design.

Requirements
Must have
• Powerpoint Slide with Title -
• Background Slide -
• It would be great to have both JPG, PNG, and Photoshop/Indesign that can be used for powerpoint, both in 4x3 ration and wide... Need Title Slide with typography and background slide for text to go over the top of.
• Stick with the theme -- Walking Unmarked Trails
• I am including our church logo, but don't feel like you need to use it in anyway.
Nice to have
• Social Media Slides - Square Slide, Facebook Header
• Greyscale Version?

```html
<!DOCTYPE html>
<html lang="en">
<head>
<meta charset="utf-8">
<title>Walking Unmarked Trails – Sermon Series Slides</title>
<link href="https://fonts.googleapis.com/css2?family=Cinzel:wght@400;700&family=Lato:wght@400;700&family=Roboto+Slab:wght@400;500&display=swap" rel="stylesheet">
<style>
  :root{
    --page:#000;
    --white:#fff;
    --rust:#6b2e12;
    --brown:#5a2a14;
    --dark-brown:#3a1a0c;
    --orange:#e07a10;
    --gold:#f2a015;
    --sage:#8aa66a;
    --band-brown:#7a4a2c;
    --body:#5a4a40;
  }
  *{box-sizing:border-box;margin:0;padding:0}
  html,body{width:1188px;height:1200px;overflow:hidden;background:var(--page)}
  .board{position:relative;width:1188px;height:1200px}
  .slide{position:absolute;width:379px;height:284px;overflow:hidden;background:var(--white)}
  .c1{left:9px}.c2{left:404px}.c3{left:799px}
  .r1{top:9px}.r2{top:308px}.r3{top:607px}.r4{top:902px}

  .photo{position:absolute}
  .band{position:absolute;left:0;right:0;bottom:0;height:7px;background:var(--sage)}
  .band.brown{background:var(--band-brown)}

  .church-name{position:absolute;display:flex;align-items:center;gap:4px;
    font:700 11px/1 "Lato",sans-serif;color:var(--brown);white-space:nowrap}
  .church-name::before{content:"";width:7px;height:7px;background:var(--sage)}
  .church-name.light{color:var(--white)}
  .church-name.small{font-size:9px}

  .series-title{position:absolute;font:500 14px/1.3 "Roboto Slab",serif;color:var(--rust);text-align:center}
  .series-title .rule{display:block;width:66px;height:1px;background:var(--rust);margin:4px auto 0}

  .display{position:absolute;font:700 20px/1.1 "Cinzel",serif;color:var(--white);letter-spacing:.2px;white-space:nowrap}
  .display.dark{color:var(--brown)}
  .display.orange{color:#c8551a;font-size:13px}
  .display.sm{font-size:16px}
  .display.caps{font-size:17px;font-variant:small-caps}
  .subtext{position:absolute;font:700 9.5px/1 "Cinzel",serif;color:var(--white);letter-spacing:.3px}
  .subtext.dark{color:var(--brown)}

  .text-block{position:absolute}
  .text-block h3{font:400 10.5px/1.2 "Lato",sans-serif;color:var(--brown);margin-bottom:2px}
  .text-block p{font:400 6.6px/1.78 "Lato",sans-serif;color:var(--body)}
  .text-block.on-dark h3{color:var(--gold)}
  .text-block.on-dark p{color:#fff}
  .text-block.orange h3{color:#d8801a}
  .panel{position:absolute}
</style>
</head>
<body>
<main class="board">

  <section class="slide c1 r1">
    <div class="photo" role="img" aria-label="Worn Bible with a cross on the cover resting on a church pew in warm light" style="inset:0;background:radial-gradient(circle at 40% 5%,#fff3d6,#f2b060 35%,#b8642a 75%,#7a3a16)"></div>
    <svg width="379" height="284" viewBox="0 0 379 284" style="position:absolute;inset:0">
      <path d="M205 0 Q140 150 220 284 L379 284 L379 0 Z" fill="#fff"/>
      <path d="M205 0 Q140 150 220 284" fill="none" stroke="#f2a015" stroke-width="8"/>
    </svg>
    <h1 class="series-title" style="left:182px;top:118px;width:195px">Walking Unmarked Trails<br>Lasting Lessons from Quiet Hills<span class="rule"></span></h1>
    <div class="church-name" style="right:10px;top:245px">Cedar Ridge Fellowship</div>
  </section>

  <section class="slide c2 r1">
    <div class="photo" role="img" aria-label="Worn Bible on a pew fading into a pale sky with crosses" style="inset:0;background:linear-gradient(90deg,#c8763a 0%,#f0b27a 40%,#f6ebe6 70%,#f3f1f1)"></div>
    <svg width="379" height="284" viewBox="0 0 379 284" style="position:absolute;inset:0">
      <path d="M205 0 Q140 150 220 284 L379 284 L379 0 Z" fill="#f6f2f1" opacity=".85"/>
      <path d="M205 0 Q140 150 220 284" fill="none" stroke="#f2a015" stroke-width="6"/>
    </svg>
    <h1 class="series-title" style="left:176px;top:122px;width:203px;color:#3a2a22">Walking Unmarked Trails<br>Lasting Lessons from Quiet Hills</h1>
    <div class="church-name" style="right:10px;top:245px">Cedar Ridge Fellowship</div>
  </section>

  <section class="slide c3 r1" style="background:linear-gradient(180deg,#f7eef0,#fff 50%)">
    <h2 class="display orange" style="left:12px;top:14px">SLIDE SECTION TITLE HERE</h2>
    <div class="church-name small" style="right:6px;top:14px">Cedar Ridge Fellowship</div>
    <div class="photo" role="img" aria-label="Person with raised arms against a golden sunset" style="left:22px;top:63px;width:143px;height:85px;background:radial-gradient(circle at 35% 55%,#ffe08a,#d9841e 35%,#3a200e 85%)"></div>
    <div class="photo" role="img" aria-label="Red brick church with a white steeple" style="left:198px;top:63px;width:143px;height:85px;background:linear-gradient(180deg,#cfe0ee 0%,#b7cde0 40%,#9a4a35 55%,#6c8a48 80%)"></div>
    <div class="text-block" style="left:22px;top:153px;width:150px">
      <h3>Subtext title here</h3>
      <p>Lorem Ipsum is simply dummy text of the printing and typesetting industry. Lorem Ipsum has been the industry's standard dummy text ever since the 1500s, when an unknown printer took a galley of type and scrambled it to make a type specimen book. It has survived not only five centuries, but also the leap into electronic typesetting, remaining essentially unchanged.</p>
    </div>
    <div class="text-block" style="left:198px;top:153px;width:150px">
      <h3>Subtext title here</h3>
      <p>Lorem Ipsum is simply dummy text of the printing and typesetting industry. Lorem Ipsum has been the industry's standard dummy text ever since the 1500s, when an unknown printer took a galley of type and scrambled it to make a type specimen book. It has survived not only five centuries, but also the leap into electronic typesetting, remaining essentially unchanged.</p>
    </div>
    <div class="band"></div>
  </section>

  <section class="slide c1 r2">
    <div class="photo" role="img" aria-label="Red Bible with a cross on its cover on a pew in glowing light" style="left:0;top:0;width:379px;height:218px;background:radial-gradient(circle at 75% 40%,#ffd27a,#e8561c 40%,#8a2810 85%)"></div>
    <h2 class="display dark sm" style="left:18px;top:234px">SLIDE SECTION TITLE HERE</h2>
    <p class="subtext dark" style="left:19px;top:256px">SUBTEXT HERE</p>
    <div class="church-name small" style="right:8px;top:246px">Cedar Ridge Fellowship</div>
    <div class="band"></div>
  </section>

  <section class="slide c2 r2">
    <div class="photo" role="img" aria-label="Weathered wooden cross against a sepia orange sky" style="left:0;top:0;width:379px;height:211px;background:radial-gradient(circle at 75% 30%,#f0b070,#c96a2a 45%,#7a3410 90%)"></div>
    <h1 class="display" style="right:18px;top:110px;text-align:right">PROJECT TITLE HERE</h1>
    <p class="subtext" style="right:18px;top:136px">SUBTEXT HERE</p>
    <div class="church-name" style="right:18px;top:236px">Cedar Ridge Fellowship</div>
    <div class="band"></div>
  </section>

  <section class="slide c3 r2" style="background:radial-gradient(circle at 50% 110%,#7a4528,#3a1a0c 60%,#2a1208)">
    <div class="photo" role="img" aria-label="Faint open Bible pages under a dark brown wash" style="left:0;right:0;bottom:7px;height:110px;background:linear-gradient(180deg,rgba(120,70,40,0),rgba(150,95,60,.45))"></div>
    <h2 class="display sm" style="left:14px;top:14px">SLIDE TITLE HERE</h2>
    <div class="church-name light small" style="right:6px;top:14px">Cedar Ridge Fellowship</div>
    <div class="text-block on-dark" style="left:26px;top:91px;width:155px">
      <h3>Subtext title here</h3>
      <p>Lorem Ipsum is simply dummy text of the printing and typesetting industry. Lorem Ipsum has been the industry's standard dummy text ever since the 1500s, when an unknown printer took a galley of type and scrambled it to make a type specimen book. It has survived not only five centuries, but also the leap into electronic typesetting, remaining essentially unchanged. It was popularised in the 1960s with the release of Typeline sheets containing Lorem Ipsum passages, and more recently with desktop publishing software.</p>
    </div>
    <div class="text-block on-dark" style="left:211px;top:91px;width:155px">
      <h3>Subtext title here</h3>
      <p>Lorem Ipsum is simply dummy text of the printing and typesetting industry. Lorem Ipsum has been the industry's standard dummy text ever since the 1500s, when an unknown printer took a galley of type and scrambled it to make a type specimen book. It has survived not only five centuries, but also the leap into electronic typesetting, remaining essentially unchanged. It was popularised in the 1960s with the release of Typeline sheets containing Lorem Ipsum passages, and more recently with desktop publishing software.</p>
    </div>
    <div class="band brown"></div>
  </section>

  <section class="slide c1 r3">
    <div class="photo" role="img" aria-label="Three crosses on a hill under a fiery orange sky" style="inset:0;background:radial-gradient(ellipse at 55% 60%,#ffb040,#ec6a12 40%,#b8300c 80%,#6a1a08)"></div>
    <h2 class="display" style="left:23px;top:110px">SLIDE SECTION TITLE HERE</h2>
    <p class="subtext" style="left:24px;top:136px">SUBTEXT HERE</p>
  </section>

  <section class="slide c2 r3">
    <h2 class="display dark sm" style="left:13px;top:12px">SLIDE TITLE HERE</h2>
    <div class="church-name small" style="right:6px;top:14px">Cedar Ridge Fellowship</div>
    <div class="text-block orange" style="left:16px;top:71px;width:192px">
      <h3>Subtext title here</h3>
      <p>Lorem Ipsum is simply dummy text of the printing and typesetting industry. Lorem Ipsum has been the industry's standard dummy text ever since the 1500s, when an unknown printer took a galley of type and scrambled it to make a type specimen book. It has survived not only five centuries, but also the leap into electronic typesetting, remaining essentially unchanged. It was popularised in the 1960s with the release of Typeline sheets containing Lorem Ipsum passages, and more recently with desktop publishing software like PageForge including versions of Lorem Ipsum. It has survived not only five centuries, but also the leap into electronic typesetting, remaining essentially unchanged.</p>
    </div>
    <div class="photo" role="img" aria-label="Red brick church with a white steeple on a green lawn" style="left:215px;top:77px;width:164px;height:140px;background:linear-gradient(180deg,#d6e4f0 0%,#bcd0e2 35%,#9a4a35 55%,#7a3a28 70%,#5e8440 85%)"></div>
    <div class="band brown"></div>
  </section>

  <section class="slide c3 r3">
    <div class="photo" role="img" aria-label="Three crosses silhouetted on a hill under a pink sunset sky" style="inset:0;background:linear-gradient(180deg,#e6a8b0 0%,#f4c8b8 40%,#c8b0ae 70%,#a8a0a0)"></div>
    <div class="church-name small" style="right:6px;top:12px">Cedar Ridge Fellowship</div>
    <div class="panel" style="left:184px;top:50px;width:194px;height:189px;background:rgba(255,255,255,.75)"></div>
    <div class="text-block" style="left:195px;top:58px;width:176px">
      <h3>Subtext title here</h3>
      <p>Lorem Ipsum is simply dummy text of the printing and typesetting industry. Lorem Ipsum has been the industry's standard dummy text ever since the 1500s, when an unknown printer took a galley of type and scrambled it to make a type specimen book. It has survived not only five centuries, but also the leap into electronic typesetting, remaining essentially unchanged. It was popularised in the 1960s with the release of Typeline sheets containing Lorem Ipsum passages, and more recently with desktop publishing software.</p>
    </div>
  </section>

  <section class="slide c1 r4">
    <div class="photo" role="img" aria-label="Wooden cross against glowing golden and violet light" style="inset:0;background:radial-gradient(circle at 55% 25%,#fff0c8,#f0c070 30%,#b0603a 60%,#5a2a4a)"></div>
    <h2 class="display dark caps" style="left:13px;top:10px">Slide Title Here</h2>
    <div class="church-name small" style="right:6px;top:12px">Cedar Ridge Fellowship</div>
    <div class="panel" style="left:0;top:82px;width:205px;height:153px;background:rgba(110,80,70,.55)"></div>
    <div class="text-block on-dark" style="left:12px;top:94px;width:185px">
      <h3 style="color:#fff">Subtext title here</h3>
      <p>Lorem Ipsum is simply dummy text of the printing and typesetting industry. Lorem Ipsum has been the industry's standard dummy text ever since the 1500s, when an unknown printer took a galley of type and scrambled it to make a type specimen book. It has survived not only five centuries, but also the leap into electronic typesetting, remaining essentially unchanged.</p>
    </div>
  </section>

  <section class="slide c2 r4">
    <div class="photo" role="img" aria-label="Faint red cross over a bright orange textured background" style="left:0;top:0;width:379px;height:211px;background:linear-gradient(120deg,#f05a14 0%,#f27a1a 45%,#f8a030 100%)"></div>
    <h1 class="display" style="right:18px;top:110px;text-align:right">PROJECT TITLE HERE</h1>
    <p class="subtext" style="right:18px;top:136px">SUBTEXT HERE</p>
    <div class="church-name" style="right:18px;top:236px">Cedar Ridge Fellowship</div>
    <div class="band"></div>
  </section>

</main>
</body>
</html>
```